Theme and starter template for small business powerpoint deck

We are starting a technology consulting company and would like to have a powerpoint/google slide theme and initial template. We are more concerned with the theme/colors at this point. Initial template can be pretty simple. We would want a cover slide, agenda slide, some content slides including text content, image content, a combination of both, etc. A closing slide. we have included jpg files of our logo, let us know if you would prefer eps/vector. I assume you may want exact color data as well?

Target Market(s)

Technology and Customer Experience Leadership at companies with 25 or more employees

Industry/Entity Type

Technology Consulting

Font styles to use
Sans Serif

Colors
0054AA
0677BA
7BADD7
CADEEF
E8F1F8

Requirements
Must have
• I have attached JPG and EPS and vector files to project. I would like to stay with those colors but open to slight variation if recommended.

```html
<!DOCTYPE html>
<html lang="en">
<head>
<meta charset="utf-8">
<title>Vantorix – Deck Theme</title>
<link href="https://fonts.googleapis.com/css2?family=Poppins:wght@500;600;700&family=Lato:wght@400;700&display=swap" rel="stylesheet">
<style>
:root{
  --navy:#0054AA;
  --ocean:#0677BA;
  --sky:#7BADD7;
  --mist:#CADEEF;
  --ice:#E8F1F8;
  --slide:#FAFCFE;
  --ink:#141414;
  --body:#4A4F57;
}
*{box-sizing:border-box;margin:0;padding:0}
html,body{width:1038px;height:1200px;overflow:hidden}
body{background:var(--ice);font-family:'Lato',sans-serif;color:var(--ink);position:relative}
.slide{position:absolute;width:478px;height:266px;background:var(--slide);border-bottom:3px solid var(--mist);overflow:hidden;box-shadow:0 1px 3px rgba(0,40,90,.06)}
.s1{left:28px;top:26px}.s2{left:533px;top:26px}
.s3{left:28px;top:324px}.s4{left:536px;top:324px}
.s5{left:28px;top:618px}.s6{left:535px;top:618px}
.s7{left:28px;top:908px}.s8{left:536px;top:908px}
.abs{position:absolute}
.marker{position:absolute;left:0;top:16px;width:10px;height:16px;background:var(--navy)}
.heading{position:absolute;left:23px;top:13px;font-family:'Poppins',sans-serif;font-weight:600;font-size:15px;letter-spacing:.2px}
.brand{position:absolute;right:24px;top:14px;font-family:'Poppins',sans-serif;font-weight:700;font-size:13px;letter-spacing:1px;color:var(--ink);display:flex;align-items:center;gap:4px}
.brand::after{content:"";width:6px;height:6px;background:var(--navy)}
.foot{position:absolute;bottom:10px;font-family:'Poppins',sans-serif;font-weight:600;font-size:5.5px;color:var(--ocean)}
.foot.date{left:24px}.foot.page{right:24px}
.txt{font-size:6.5px;line-height:1.9;color:var(--body)}
.photo{position:absolute;border-radius:3px}
.ph-a{background:linear-gradient(160deg,#3A78C0,#0D3A78)}
.ph-b{background:linear-gradient(160deg,#9CC0E0,#4C7FB0)}
.ph-c{background:linear-gradient(160deg,#2A8CC8,#0B4E86)}
/* cover */
.cover-brand{left:23px;top:30px;right:auto;font-size:17px}
.welcome{left:23px;top:88px;font-family:'Poppins',sans-serif;font-weight:600;font-size:9.5px}
.cover-title{left:22px;top:100px;font-family:'Poppins',sans-serif;font-weight:700;font-size:33px;letter-spacing:.5px}
.cover-lede{left:23px;top:148px;width:172px;font-size:7.5px;line-height:1.65;color:#333}
.cover-date{left:24px;top:199px;font-size:8.5px;color:var(--ocean)}
/* agenda */
.ag-item{position:absolute;display:flex;gap:8px;width:190px}
.ag-num{font-family:'Poppins',sans-serif;font-weight:600;font-size:12px;width:12px;padding-top:6px;text-align:right}
.ag-body{border-left:1px solid var(--mist);padding-left:8px}
.ag-title{font-family:'Poppins',sans-serif;font-weight:600;font-size:8.5px;color:var(--navy)}
.ag-desc{font-size:5.5px;line-height:1.8;color:#444;margin-top:2px}
/* about */
.about-copy{left:240px;top:54px;width:200px}
.about-copy p+p{margin-top:8px}
.stats{left:241px;top:172px;display:flex;align-items:center}
.stat{width:43px;height:43px;background:#fff;text-align:center;font-size:5.5px;color:#333;padding-top:8px;box-shadow:0 1px 3px rgba(0,40,90,.1)}
.stat b{display:block;font-family:'Poppins',sans-serif;font-weight:500;font-size:9.5px;margin-bottom:4px;color:var(--ink)}
.stat.hi{width:52px;height:51px;background:var(--navy);color:#fff;padding-top:10px}
.stat.hi b{color:#fff;font-size:11px}
/* services */
.svc{position:absolute;top:71px;width:114px;text-align:center}
.svc-img{width:114px;height:86px;border:1px solid var(--sky)}
.svc h4{font-weight:700;font-size:7px;margin-top:9px}
.svc p{font-size:5.5px;line-height:1.7;color:var(--body);margin-top:3px}
/* graph */
.big-num{font-family:'Poppins',sans-serif;font-weight:500;font-size:18px}
.graph-side{left:364px;top:67px;width:91px;text-align:justify;font-size:6.5px;line-height:1.9;color:#222}
.graph-side p+p{margin-top:10px}
.graph-cap{left:120px;top:196px;width:220px;font-size:7px;line-height:2.1;color:#222}
/* why */
.why-left{left:24px;top:50px;width:200px;text-align:justify;font-size:6px;line-height:2;color:#222}
.why-left p+p{margin-top:9px}
.why-rule{left:240px;top:55px;width:1px;height:190px;background:var(--mist)}
.why-list{left:262px;top:50px;width:194px;list-style:none;font-size:6px;line-height:2.2;color:#222}
.why-list li{margin-bottom:4px;text-indent:11px;position:relative}
.why-list li::before{content:"";position:absolute;left:-11px;top:4px;width:6px;height:5px;background:var(--navy)}
/* statistics */
.stat-copy{left:24px;top:54px;width:312px;font-size:6.5px;line-height:1.9;color:var(--body)}
.ring{position:absolute;top:112px;width:64px;text-align:center}
.ring span{position:absolute;left:0;top:18px;width:64px;font-family:'Poppins',sans-serif;font-weight:500;font-size:19px}
.ring p{font-size:7.5px;margin-top:12px;color:var(--ink)}
.panel{left:353px;top:0;width:125px;height:266px;background:var(--navy);color:#fff}
.panel .brand{left:11px;right:auto;top:15px;color:#fff}
.panel .brand::after{background:#fff}
.panel-copy{position:absolute;left:13px;top:48px;width:100px;text-align:justify;font-size:6px;line-height:2.1;color:var(--ice)}
.panel-copy p+p{margin-top:10px}
.panel .foot{color:#fff;right:24px}
/* contact */
.close-brand{left:46px;top:106px;right:auto;font-size:21px}
.close-brand::after{width:9px;height:9px}
.thanks{left:78px;top:148px;font-family:'Poppins',sans-serif;font-weight:600;font-size:12px}
.divider{left:237px;top:50px;width:1px;height:168px;background:var(--mist)}
.contact-h{left:276px;top:60px;font-family:'Poppins',sans-serif;font-weight:700;font-size:14px}
.c-row{position:absolute;left:278px;display:flex;align-items:center;gap:9px;font-size:10px;color:#111}
.c-ico{width:20px;height:20px;border-radius:50%;background:var(--navy);display:flex;align-items:center;justify-content:center}
</style>
</head>
<body>

<!-- 01 cover -->
<section class="slide s1">
  <div class="brand cover-brand">VANTORIX</div>
  <div class="abs welcome">WELCOME TO</div>
  <h1 class="abs cover-title">VANTORIX</h1>
  <p class="abs cover-lede">Lorem ipsum dolor sit amet, consectetur adipiscing elit, sed do eiusmod tempor incididunt ut labore et dolore magna aliqua.</p>
  <div class="abs cover-date">08 Augest 2024</div>
  <div class="photo ph-a" style="left:230px;top:32px;width:118px;height:205px" role="img" aria-label="Photo of a team meeting in a boardroom"></div>
  <div class="photo ph-b" style="left:354px;top:32px;width:100px;height:100px" role="img" aria-label="Photo of a smiling consultant at a desk"></div>
  <div class="photo ph-c" style="left:354px;top:137px;width:100px;height:100px" role="img" aria-label="Photo of a business advisor in a suit"></div>
</section>

<!-- 02 agenda -->
<section class="slide s2">
  <span class="marker"></span>
  <h2 class="heading">AGENDA</h2>
  <div class="brand">VANTORIX</div>
  <div class="ag-item" style="left:36px;top:64px"><span class="ag-num">1</span><div class="ag-body"><div class="ag-title">ABOUT VANTORIX</div><div class="ag-desc">Itaque earum rerum hic tenetur a sapiente delectus, ut aut reiciendis voluptatibus</div></div></div>
  <div class="ag-item" style="left:251px;top:64px"><span class="ag-num">2</span><div class="ag-body"><div class="ag-title">OUR SERVICES</div><div class="ag-desc">Itaque earum rerum hic tenetur a sapiente delectus, ut aut reiciendis voluptatibus</div></div></div>
  <div class="ag-item" style="left:36px;top:118px"><span class="ag-num">3</span><div class="ag-body"><div class="ag-title">OUR GRAPH</div><div class="ag-desc">Itaque earum rerum hic tenetur a sapiente delectus, ut aut reiciendis voluptatibus</div></div></div>
  <div class="ag-item" style="left:251px;top:118px"><span class="ag-num">4</span><div class="ag-body"><div class="ag-title">WHY CHOOSE US</div><div class="ag-desc">Itaque earum rerum hic tenetur a sapiente delectus, ut aut reiciendis voluptatibus</div></div></div>
  <div class="ag-item" style="left:36px;top:172px"><span class="ag-num">5</span><div class="ag-body"><div class="ag-title">STATISTICS</div><div class="ag-desc">Itaque earum rerum hic tenetur a sapiente delectus, ut aut reiciendis voluptatibus</div></div></div>
  <div class="ag-item" style="left:251px;top:172px"><span class="ag-num">6</span><div class="ag-body"><div class="ag-title">CONTACT US</div><div class="ag-desc">Itaque earum rerum hic tenetur a sapiente delectus, ut aut reiciendis voluptatibus</div></div></div>
  <div class="foot date">08 AUGEST 2024</div><div class="foot page">PAGE NO: 02</div>
</section>

<!-- 03 about -->
<section class="slide s3">
  <span class="marker"></span>
  <h2 class="heading">ABOUT VANTORIX</h2>
  <div class="brand">VANTORIX</div>
  <div class="photo ph-a" style="left:24px;top:62px;width:181px;height:76px" role="img" aria-label="Photo of a team meeting around a table"></div>
  <div class="photo ph-b" style="left:24px;top:143px;width:88px;height:78px" role="img" aria-label="Photo of a presenter speaking to colleagues"></div>
  <div class="photo ph-c" style="left:117px;top:143px;width:88px;height:78px" role="img" aria-label="Photo of a smiling consultant"></div>
  <div class="abs about-copy txt">
    <p>Lorem ipsum dolor sit amet, consectetur adipiscing elit, sed do eiusmod tempor incididunt ut labore et dolore magna aliqua. Ut enim ad minim veniam, quis nostrud exercitation ullamco laboris nisi ut aliquip ex ea commodo consequat.</p>
    <p>Duis aute irure dolor in reprehenderit in voluptate velit esse cillum dolore eu fugiat nulla pariatur. Excepteur sint occaecat cupidatat non proident.</p>
  </div>
  <div class="abs stats">
    <div class="stat"><b>12+</b>Partners</div>
    <div class="stat hi"><b>13k</b>Satisy Customer</div>
    <div class="stat" style="width:44px"><b>15+</b>Certificate</div>
  </div>
  <div class="foot date">08 AUGEST 2024</div><div class="foot page">PAGE NO: 03</div>
</section>

<!-- 04 services -->
<section class="slide s4">
  <span class="marker"></span>
  <h2 class="heading">OUR SERVICES</h2>
  <div class="brand">VANTORIX</div>
  <div class="svc" style="left:36px"><div class="svc-img" role="img" aria-label="Photo of two colleagues reviewing work at a desk" style="background:linear-gradient(135deg,#E8F1F8,#7BADD7)"></div><h4>Lorem ipsum dolor</h4><p>Excepteur sint occaecat cupidatat non proident, sunt in culpa qui officia deserunt mollit .</p></div>
  <div class="svc" style="left:185px"><div class="svc-img" role="img" aria-label="Photo of a team discussion around a meeting table" style="background:linear-gradient(135deg,#CADEEF,#0677BA)"></div><h4>Lorem ipsum dolor</h4><p>Excepteur sint occaecat cupidatat non proident, sunt in culpa qui officia deserunt mollit .</p></div>
  <div class="svc" style="left:334px"><div class="svc-img" role="img" aria-label="Photo of two colleagues reading a document together in an office" style="background:linear-gradient(135deg,#7BADD7,#0054AA)"></div><h4>Lorem ipsum dolor</h4><p>Excepteur sint occaecat cupidatat non proident, sunt in culpa qui officia deserunt mollit .</p></div>
  <div class="foot date">08 AUGEST 2024</div><div class="foot page">PAGE NO: 04</div>
</section>

<!-- 05 graph -->
<section class="slide s5">
  <span class="marker"></span>
  <h2 class="heading">OUR GRAPH</h2>
  <div class="brand">VANTORIX</div>
  <div class="abs" style="left:32px;top:82px;text-align:center">
    <div class="big-num" style="color:var(--navy)">657</div>
    <div style="font-size:7px;color:var(--navy);margin-top:-2px">Excepteur sint</div>
  </div>
  <div class="abs" style="left:23px;top:133px;text-align:center">
    <div class="big-num" style="color:var(--sky)">472</div>
    <div style="font-size:7px;color:var(--sky);margin-top:-2px">Duis aute iruret</div>
  </div>
  <svg class="abs" style="left:116px;top:68px" width="220" height="128" aria-label="Bar chart F1 to F6">
    <g fill="#7BADD7">
      <rect x="7" y="45" width="20" height="54"/>
      <rect x="42" y="27" width="20" height="72"/>
      <rect x="80" y="67" width="20" height="32"/>
      <rect x="116" y="62" width="20" height="37"/>
      <rect x="152" y="26" width="20" height="73"/>
    </g>
    <rect x="190" y="0" width="20" height="99" fill="#0054AA"/>
    <line x1="0" y1="99.5" x2="218" y2="99.5" stroke="#CADEEF" stroke-width="1"/>
    <g font-family="Lato,sans-serif" font-size="6" fill="#333" text-anchor="middle">
      <text x="17" y="112">F1</text><text x="52" y="112">F2</text><text x="90" y="112">F3</text>
      <text x="126" y="112">F4</text><text x="162" y="112">F5</text><text x="200" y="112">F6</text>
    </g>
  </svg>
  <div class="abs graph-side">
    <p>Duis aute irure dolor in reprehenderit in voluptate velit esse cillum dolore eu fugiat nulla pariatur.</p>
    <p>Excepteur sint occaecat cupidatat non proident, sunt in culpa qui officia deserunt mollit anim id est laborum.</p>
  </div>
  <p class="abs graph-cap">Excepteur sint occaecat cupidatat non proident, sunt in culpa qui officia deserunt mollit anim id est laborum.</p>
  <div class="foot date">08 AUGEST 2024</div><div class="foot page">PAGE NO: 05</div>
</section>

<!-- 06 why choose us -->
<section class="slide s6">
  <span class="marker"></span>
  <h2 class="heading">WHY CHOOSE US</h2>
  <div class="brand">VANTORIX</div>
  <div class="abs why-left">
    <p>At vero eos et accusamus et iusto odio dignissimos ducimus qui blanditiis praesentium voluptatum deleniti atque corrupti quos dolores et quas molestias excepturi sint occaecati cupiditate non provident, similique sunt in culpa qui officia deserunt mollitia animi, id est laborum et dolorum fuga.</p>
    <p>Nam libero tempore, cum soluta nobis est eligendi optio cumque e possimus, omnis voluptas assumenda est, omnis dolor repellendus. Temporibus autem quibusdam et aut officiis debitis aut rerum necessitatibus saepe eveniet ut et voluptates repudiandae sint et molestiae non recusandae.</p>
    <p>Itaque earum rerum hic tenetur a sapiente delectus, ut aut reiciendis voluptatibus maiores alias consequatur aut perferendis doloribus asperiores repellat.</p>
  </div>
  <div class="abs why-rule"></div>
  <ul class="abs why-list">
    <li>Temporibus autem quibusdam et aut officiis debitis aut rerum necessitatibus saepe eveniet ut et voluptates repudiandae sinte stiae non recusandae.</li>
    <li>Temporibus autem quibusdam et aut officiis debitis aut rerum necessitatibus saepe eveniet ut et voluptates repudiandae sinte stiae non recusandae.</li>
    <li>Temporibus autem quibusdam et aut officiis debitis aut rerum necessitatibus saepe eveniet ut et voluptates repudiandae sinte stiae non recusandae.</li>
    <li>Temporibus autem quibusdam et aut officiis debitis aut rerum necessitatibus saepe eveniet ut et voluptates reiciendis voluptatibus maiores alias consequatur autrepudiandae sintestiae non recusandae.</li>
  </ul>
  <div class="foot date">08 AUGEST 2024</div><div class="foot page">PAGE NO: 06</div>
</section>

<!-- 07 statistics -->
<section class="slide s7">
  <span class="marker"></span>
  <h2 class="heading">STATISTICS</h2>
  <p class="abs stat-copy">Lorem ipsum dolor sit amet, consectetur adipiscing elit, sed do eiusmod tempor incididunt ut labore et dolore magna aliqua. Ut enim ad minim veniam, quis nostrud exercitation ullamco laboris nisi ut aliquip ex ea commodo consequat.</p>
  <div class="ring" style="left:23px">
    <svg width="64" height="64"><circle cx="32" cy="32" r="28" fill="none" stroke="#CADEEF" stroke-width="4"/><circle cx="32" cy="32" r="28" fill="none" stroke="#0054AA" stroke-width="4" stroke-dasharray="110 176" transform="rotate(0 32 32)"/></svg>
    <span>35</span><p>Lorem ipsum</p>
  </div>
  <div class="ring" style="left:128px">
    <svg width="64" height="64"><circle cx="32" cy="32" r="28" fill="none" stroke="#CADEEF" stroke-width="4"/><circle cx="32" cy="32" r="28" fill="none" stroke="#0054AA" stroke-width="4" stroke-dasharray="127 176" transform="rotate(-90 32 32)"/></svg>
    <span>72</span><p>Lorem ipsum</p>
  </div>
  <div class="ring" style="left:233px">
    <svg width="64" height="64"><circle cx="32" cy="32" r="28" fill="none" stroke="#CADEEF" stroke-width="4"/><circle cx="32" cy="32" r="28" fill="none" stroke="#0054AA" stroke-width="4" stroke-dasharray="167 176" transform="rotate(-80 32 32)"/></svg>
    <span>95</span><p>Lorem ipsum</p>
  </div>
  <div class="abs panel">
    <div class="brand">VANTORIX</div>
    <div class="panel-copy">
      <p>Lorem ipsum dolor sit amet, consectetur adipiscing elit, sed do eiusmod tempor incididunt ut labore et dolore magna aliqua. Ut enim ad minim veniam, quis nostrud exercitation ullamco laboris nisi ut aliquip ex ea commodo consequat.</p>
      <p>Duis aute irure dolor in reprehenderit in voluptate velit esse cillum dolore eu fugiat nulla pariatur. Excepteur sint occaecat cupidatat non proident, sunt in culpa qui officia deserunt mollit anim id est laborum.</p>
    </div>
    <div class="foot page">PAGE NO: 07</div>
  </div>
  <div class="foot date">08 AUGEST 2024</div>
</section>

<!-- 08 contact -->
<section class="slide s8">
  <span class="marker"></span>
  <h2 class="heading">GET IN TOUCH WITH US</h2>
  <div class="brand close-brand">VANTORIX</div>
  <div class="abs thanks">THANK YOU</div>
  <div class="abs divider"></div>
  <div class="abs contact-h">CONTACT US</div>
  <div class="c-row" style="top:94px"><span class="c-ico"><svg width="10" height="10" viewBox="0 0 10 10"><path d="M5 .5a3.3 3.3 0 0 0-3.3 3.3C1.7 6.2 5 9.5 5 9.5s3.3-3.3 3.3-5.7A3.3 3.3 0 0 0 5 .5z" fill="#fff"/><circle cx="5" cy="3.8" r="1.2" fill="#0054AA"/></svg></span>Vantorix, United States</div>
  <div class="c-row" style="top:135px"><span class="c-ico"><svg width="10" height="10" viewBox="0 0 10 10"><path d="M2.2 .8l1.6 1.9-.9 1.2a6 6 0 0 0 3.2 3.2l1.2-.9 1.9 1.6-.8 1.4C5 9.5.5 5 .8 1.6z" fill="#fff"/></svg></span>+1 555 010 2040</div>
  <div class="c-row" style="top:172px"><span class="c-ico"><svg width="10" height="8" viewBox="0 0 10 8"><rect x=".5" y=".5" width="9" height="7" rx="1" fill="#fff"/><path d="M.8 1l4.2 3.2L9.2 1" stroke="#0054AA" stroke-width=".9" fill="none"/></svg></span>info@vantorix.com</div>
  <div class="foot date">08 AUGEST 2024</div><div class="foot page">PAGE NO: 08</div>
</section>

</body>
</html>
```